Tessmar Fahrwerkstatt
Sehr angenehme zusammenarbeit nicht aufdringlich und genau auf die Wünsche eingegangen. Wir werde sicher noch mehr zusammen Arbeiten. Gruss Lukas Hegemann Inhaber Tessmar Fahrwerkstatt
Zielgruppe
Dinks und Kunden mit viel Erfolg und hohem Ausgabepotential.
Aufgabenstellung
Unsere Firma vertreibt Fahrzeuge im Luxusbereich hauptgebiet Valmerra aber auch andere Sportwagen. Was uns fehlt ist ein optischer Wiedererkennugswert. Deshalb hätten wir gerne ein Visitenkarten Design und Briefpapier Design. Später soll auch noch eine Webseite mit gleichem Wiedererkennungswert entstehen. " Roter Faden "

```html
<!DOCTYPE html>
<html lang="de">
<head>
<meta charset="utf-8">
<title>Tessmar Fahrwerkstatt – Visitenkarte</title>
<link href="https://fonts.googleapis.com/css2?family=Open+Sans:wght@300;400&display=swap" rel="stylesheet">
<style>
  :root {
    --backdrop: #e9e6e2;
    --navy: #0f1c4d;
    --navy-deep: #0a1438;
    --navy-glow: #24387a;
    --card-white: #ffffff;
    --ink-grey: #6f6f73;
    --divider: #d6d6d9;
    --brand-ink: #0f1c4d;
  }
  * { box-sizing: border-box; margin: 0; padding: 0; }
  html, body {
    width: 1200px;
    height: 800px;
    overflow: hidden;
  }
  body {
    background: var(--backdrop);
    font-family: "Open Sans", Arial, sans-serif;
    position: relative;
  }
  .card {
    position: absolute;
    top: 245px;
    width: 500px;
    height: 310px;
    box-shadow: 0 6px 18px rgba(0, 0, 0, 0.18);
  }
  .card-front {
    left: 70px;
    background: radial-gradient(ellipse at 45% 35%, var(--navy-glow) 0%, var(--navy) 45%, var(--navy-deep) 100%);
    display: flex;
    align-items: center;
    justify-content: center;
  }
  .card-back {
    left: 630px;
    background: var(--card-white);
    display: flex;
  }
  .brand-name {
    font-weight: 400;
    text-transform: uppercase;
    letter-spacing: 0.12em;
    line-height: 1.25;
  }
  .card-front .brand-name {
    color: var(--card-white);
    font-size: 30px;
    text-align: left;
  }
  .back-brand {
    width: 235px;
    padding: 42px 0 0 30px;
  }
  .card-back .brand-name {
    color: var(--brand-ink);
    font-size: 18px;
  }
  .back-divider {
    width: 1px;
    background: linear-gradient(to bottom, var(--divider) 0%, var(--divider) 80%, rgba(214,214,217,0) 100%);
    margin: 18px 0 18px;
  }
  .contact {
    padding: 54px 0 0 20px;
    font-weight: 300;
    font-size: 13px;
    line-height: 1.45;
    color: var(--ink-grey);
  }
  .contact-block { margin-bottom: 16px; }
  .contact-block p { white-space: nowrap; }
</style>
</head>
<body>
  <section class="card card-front" aria-label="Visitenkarte Vorderseite">
    <p class="brand-name">Tessmar<br>Fahrwerkstatt</p>
  </section>

  <section class="card card-back" aria-label="Visitenkarte Rückseite">
    <div class="back-brand">
      <p class="brand-name">Tessmar<br>Fahrwerkstatt</p>
    </div>
    <div class="back-divider"></div>
    <div class="contact">
      <div class="contact-block">
        <p>Marlene Ostrowski</p>
        <p>Geschäftsführerin</p>
      </div>
      <div class="contact-block">
        <p>Lindenweg 27</p>
        <p>43512 Harbeck</p>
      </div>
      <div class="contact-block">
        <p>Tel.: +49 (0)30 5550184</p>
        <p>Mobil: +49 (0)170 5550392</p>
        <p>Fax: +49 (0)30 5550185</p>
        <p>E-Mail: info@tessmar-fahrwerk.de</p>
      </div>
    </div>
  </section>
</body>
</html>
```